ONE PAGE WEBSITE for Zesty Recruitment Agency

Hello creative gurus,

We're are after a ONE PAGE World Press web design.

We're a recruitment start-up specializing in Information Technology.

The design should be cool, quirky and NOT mainstream.

The kind of web designs we like:

http://www.vantorix.co.za/#what-we-do
http://quillandmoss.com/
http://www.kelvado.com/index.html#home
http://marcellobrantovi.com/#/selected-works

And, we only like the front page of this web site: http://www.zenbyglim.com/

Any questions, please do let us know!

Thank you, and happy creating!

Robin

Reason: Just need a day or two to finalize everything. Thanks, Robin

Target Market(s)

Companies, employees, candidates

Industry/Entity Type

Recruitment

Coding

Coded - Design and coding required

Colors
f37122
f68e4e
ffcf3e
00a990
86cfc6
fcca95
fee18a

Requirements
Must have
• 1. The website should be techy, cool, funky, quirky and user-friendly.
• 2. Mobile-compatible
• 3. Please use our spaceman logo through the website (attached).
• 4. Please see attached website content/brief.
• 5. Colors - orange color is a must, but please use other colors to spice it up - make it more fun.
• The kind of web designs we like:
• http://www.vantorix.co.za/#what-we-do
• http://quillandmoss.com/
• http://www.kelvado.com/index.html#home
• http://marcellobrantovi.com/#/selected-works
• http://www.zenbyglim.com/
• Any questions, please do let us know!
Should not have
• -NO stock image banners, photos, images

```html
<!DOCTYPE html>
<html lang="en">
<head>
<meta charset="utf-8">
<title>Zestio Talent</title>
<link href="https://fonts.googleapis.com/css2?family=Lato:wght@400;700;900&family=Open+Sans:wght@400;600;700&family=Roboto:wght@400;500&display=swap" rel="stylesheet">
<style>
:root{
  --orange:#f37122;
  --orange-soft:#f68e4e;
  --ink:#3a3a3a;
  --text:#555;
  --grey-bg:#f1f1f1;
  --dark:#1f2328;
  --white:#fff;
  --hero-dark:#2b2e33;
}
*{margin:0;padding:0;box-sizing:border-box}
html,body{width:1200px;height:3000px;overflow:hidden}
body{position:relative;font-family:'Open Sans',sans-serif;color:var(--text);background:var(--white)}
.abs{position:absolute}

/* sidebar */
.sidebar{left:0;top:0;width:274px;height:3000px;background:var(--orange)}
.brand-box{left:0;top:0;width:274px;height:120px;background:var(--white);display:flex;align-items:center;padding-left:24px;gap:12px}
.brand-dot{width:44px;height:44px;border-radius:50%;background:var(--ink)}
.brand-name{font-family:'Lato',sans-serif;font-weight:900;font-size:30px;letter-spacing:1px;color:var(--ink)}
.nav{left:0;top:132px;width:262px;list-style:none}
.nav li{height:50px;display:flex;align-items:center;padding-left:18px;border-bottom:1px solid rgba(255,255,255,.35);color:var(--white);font-family:'Open Sans',sans-serif;font-weight:700;font-size:15px;letter-spacing:.3px}
.nav li svg{width:16px;height:16px;margin-right:16px}
.nav li .chev{margin-left:auto;margin-right:14px;font-weight:400;font-size:16px}
.side-social{left:40px;top:540px;display:flex;gap:18px}
.diamond-btn{width:56px;height:56px;display:flex;align-items:center;justify-content:center;position:relative}
.diamond-btn::before{content:"";position:absolute;width:38px;height:38px;border:2px solid var(--white);transform:rotate(45deg)}
.diamond-btn span{width:8px;height:8px;background:var(--white);border-radius:50%}

/* hero */
.hero{left:274px;top:0;width:926px;height:502px;background:linear-gradient(135deg,#4a4d52,#2a2c30 55%,#3b3d41)}
.hero h1{position:absolute;left:0;width:926px;top:136px;text-align:center;font-family:'Lato',sans-serif;font-weight:900;font-size:48px;color:var(--white);letter-spacing:.5px}
.hero p{position:absolute;left:250px;width:426px;top:222px;text-align:center;color:var(--white);font-size:14px;line-height:26px}
.hero-arrows{position:absolute;left:405px;top:320px;display:flex;gap:14px}
.arrow{width:54px;height:54px;display:flex;align-items:center;justify-content:center;position:relative}
.arrow::before{content:"";position:absolute;width:36px;height:36px;border:2px solid var(--white);transform:rotate(45deg)}
.arrow.active::before{background:var(--orange);border-color:var(--orange)}
.arrow svg{position:relative;width:14px;height:14px}

/* section titles */
.sec-title{position:absolute;left:274px;width:926px;text-align:center;font-family:'Lato',sans-serif;font-weight:700;font-size:30px;color:var(--orange)}
.sec-rule{position:absolute;left:652px;width:170px;height:2px;background:var(--orange)}

/* why */
.feature{position:absolute;top:660px;width:250px;text-align:center}
.feature .gem{width:180px;height:180px;margin:0 auto;position:relative;display:flex;align-items:center;justify-content:center}
.feature .gem::before{content:"";position:absolute;width:150px;height:150px;transform:rotate(45deg);outline:3px solid var(--ink);outline-offset:5px;background:var(--ink)}
.feature.hot .gem::before{background:var(--orange);outline-color:var(--orange)}
.feature .gem svg{position:relative;width:60px;height:60px}
.feature h3{margin-top:28px;font-family:'Roboto',sans-serif;font-weight:500;font-size:18px;color:#222}
.feature.hot h3{color:var(--orange)}
.feature p{margin-top:12px;font-size:12.5px;line-height:20px;color:#444}
.read-more{display:inline-block;margin-top:16px;color:var(--orange);font-weight:600;font-size:14px}

/* split panels */
.photo{position:absolute}
.panel{position:absolute;background:var(--grey-bg)}
.panel h2{font-family:'Lato',sans-serif;font-weight:700;font-size:19px;color:var(--orange)}
.panel p{font-size:13px;line-height:22px;color:#444;margin-top:12px}
.ticks{list-style:none;margin-top:14px}
.ticks li{display:flex;align-items:center;gap:12px;font-weight:600;font-size:14px;color:var(--orange);height:40px}
.ticks svg{width:22px;height:22px}
.reasons{list-style:none;margin-top:22px}
.reasons li{position:relative;padding-left:26px;font-size:13px;line-height:22px;color:#444;margin-bottom:14px}
.reasons li::before{content:"";position:absolute;left:0;top:5px;width:12px;height:12px;border-radius:50%;border:2px solid var(--orange)}
.reasons b{color:var(--orange);font-weight:600}

/* founder */
.portrait{left:296px;top:1852px;width:176px;height:176px;border-radius:50%;border:4px solid var(--orange);background:radial-gradient(circle at 50% 40%,#e9d7c7,#c9b6a6 60%,#8d8a94)}
.founder{left:498px;top:1842px;width:680px}
.founder h2{font-family:'Lato',sans-serif;font-weight:700;font-size:23px;color:var(--orange);letter-spacing:.5px}
.founder .rule{width:170px;height:2px;background:var(--orange);margin-top:12px}
.founder .lead{margin-top:18px;font-weight:600;font-size:15px;color:var(--orange)}
.founder p{margin-top:12px;font-size:13px;line-height:22px;color:#444}

/* blog */
.blog{left:274px;top:2104px;width:926px;height:570px;background:var(--grey-bg)}
.card{position:absolute;top:2244px;width:276px;text-align:center}
.card .img{width:276px;height:200px;position:relative}
.card .date{position:absolute;left:0;bottom:0;width:46px;height:60px;font-family:'Roboto',sans-serif;font-weight:500;font-size:13px;color:var(--white);text-align:center}
.card .date .m{height:30px;line-height:30px;background:var(--ink)}
.card .date .d{height:30px;line-height:30px;background:var(--orange)}
.card h3{margin-top:24px;font-family:'Roboto',sans-serif;font-weight:500;font-size:17px;color:#222}
.card p{margin-top:14px;font-size:11.5px;line-height:20px;color:#555;padding:0 6px}
.btn{display:inline-block;margin-top:14px;width:104px;height:36px;line-height:32px;border-radius:18px;border:2px solid #333;font-weight:600;font-size:12.5px;color:#333}
.btn.filled{background:var(--orange);border-color:var(--orange);color:var(--white)}

/* footer */
.footer{left:274px;top:2674px;width:926px;height:326px;background:var(--dark)}
.foot-brand{left:308px;top:2738px;display:flex;align-items:center;gap:14px}
.foot-brand .brand-dot{width:62px;height:62px;background:var(--white)}
.foot-brand .brand-name{color:var(--white);font-size:34px;font-weight:700;letter-spacing:3px}
.foot-social{left:330px;top:2846px;display:flex;gap:14px}
.contact-title{left:756px;top:2730px;font-family:'Lato',sans-serif;font-weight:700;font-size:25px;color:var(--white)}
.contact-rule{left:756px;top:2770px;width:116px;height:2px;background:var(--white)}
.contact-line{left:756px;display:flex;align-items:center;gap:16px;color:var(--white);font-size:16px}
.contact-line b{font-weight:700}
.contact-line .ico{width:38px;height:38px;position:relative;display:flex;align-items:center;justify-content:center}
.contact-line .ico::before{content:"";position:absolute;width:26px;height:26px;border:2px solid var(--white);transform:rotate(45deg)}
.contact-line svg{position:relative;width:15px;height:15px}
.foot-rule{left:308px;top:2938px;width:866px;height:1px;background:rgba(255,255,255,.2)}
.copyright{left:274px;top:2960px;width:926px;text-align:center;color:var(--white);font-size:13px}
</style>
</head>
<body>

<aside class="abs sidebar"></aside>
<div class="abs brand-box"><span class="brand-dot"></span><span class="brand-name">ZESTIO</span></div>
<ul class="abs nav">
  <li><svg viewBox="0 0 16 16"><path d="M2 8 8 2l6 6h-2v6H9v-4H7v4H4V8z" fill="#fff"/></svg>HOME<span class="chev">›</span></li>
  <li><svg viewBox="0 0 16 16"><rect x="3" y="1" width="10" height="14" fill="none" stroke="#fff" stroke-width="2"/><path d="M6 5h4M6 8h4M6 11h4" stroke="#fff"/></svg>COMPANIES<span class="chev">›</span></li>
  <li><svg viewBox="0 0 16 16"><circle cx="8" cy="5" r="3.5" fill="#fff"/><path d="M2 15c0-4 3-6 6-6s6 2 6 6z" fill="#fff"/></svg>TALENT<span class="chev">›</span></li>
  <li><svg viewBox="0 0 16 16"><rect x="2" y="1" width="12" height="14" fill="none" stroke="#fff" stroke-width="2"/><path d="M5 5h6M5 8h6M5 11h4" stroke="#fff"/></svg>REFERALS<span class="chev">›</span></li>
  <li><svg viewBox="0 0 16 16"><rect x="1" y="3" width="14" height="10" fill="none" stroke="#fff" stroke-width="2"/><path d="M1 3l7 6 7-6" fill="none" stroke="#fff" stroke-width="1.5"/></svg>ABOUT US<span class="chev">›</span></li>
  <li><svg viewBox="0 0 16 16"><ellipse cx="7" cy="7" rx="6" ry="4.5" fill="none" stroke="#fff" stroke-width="2"/><path d="M4 11l-2 4 5-3" fill="#fff"/></svg>BLOG<span class="chev">›</span></li>
  <li><svg viewBox="0 0 16 16"><path d="M3 1l3 3-2 2c1 2 3 4 5 5l2-2 3 3-2 3C7 15 1 9 1 3z" fill="#fff"/></svg>CONTACT US<span class="chev">›</span></li>
</ul>
<div class="abs side-social">
  <div class="diamond-btn"><span></span></div>
  <div class="diamond-btn"><span></span></div>
  <div class="diamond-btn"><span></span></div>
</div>

<section class="abs hero" role="img" aria-label="Team meeting around an office table, darkened backdrop">
  <h1>WELCOME TO ZESTIO TALENT</h1>
  <p>We're Sydney's IT talent specialists. We are passionate, with boundless energy, and work to bring great people together.</p>
  <div class="hero-arrows">
    <div class="arrow"><svg viewBox="0 0 14 14"><path d="M9 2 4 7l5 5" fill="none" stroke="#fff" stroke-width="2"/></svg></div>
    <div class="arrow active"><svg viewBox="0 0 14 14"><path d="M5 2l5 5-5 5" fill="none" stroke="#fff" stroke-width="2"/></svg></div>
  </div>
</section>

<h2 class="sec-title" style="top:552px">WHY WORK WITH US?</h2>
<div class="sec-rule" style="top:602px"></div>

<div class="feature" style="left:315px">
  <div class="gem"><svg viewBox="0 0 60 60"><circle cx="21" cy="20" r="8" fill="#fff"/><circle cx="39" cy="20" r="8" fill="#fff"/><path d="M6 48c0-10 7-16 15-16s15 6 15 16zM28 48c0-10 5-16 11-16s15 6 15 16z" fill="#fff"/></svg></div>
  <h3>Experts</h3>
  <p>We're experts in our field and have years of hands-on experience in the I.T. industry. We know our market.</p>
  <span class="read-more">Read More ➜</span>
</div>
<div class="feature hot" style="left:587px">
  <div class="gem"><svg viewBox="0 0 60 60"><circle cx="32" cy="18" r="9" fill="none" stroke="#fff" stroke-width="5" stroke-dasharray="4 3"/><circle cx="32" cy="18" r="4" fill="#fff"/><path d="M6 40h12l10 4h12l12-8 2 4-14 12H26l-10-4H6z" fill="#fff"/></svg></div>
  <h3>Bespoke Service</h3>
  <p>We offer a bespoke service with dedicated account manager (a nice one!) who will stay in regular contact.</p>
  <span class="read-more">Read More ➜</span>
</div>
<div class="feature" style="left:897px">
  <div class="gem"><svg viewBox="0 0 60 60"><circle cx="26" cy="26" r="16" fill="none" stroke="#fff" stroke-width="5"/><circle cx="26" cy="23" r="5" fill="#fff"/><path d="M17 34c2-5 5-6 9-6s7 1 9 6" fill="#fff"/><path d="M38 38l12 12" stroke="#fff" stroke-width="7" stroke-linecap="round"/></svg></div>
  <h3>Recruitment Process</h3>
  <p>We walk in your shoes. We've been on the other side of the recruitment process your side and we understand.</p>
  <span class="read-more">Read More ➜</span>
</div>

<div class="photo" style="left:274px;top:1056px;width:462px;height:360px;background:linear-gradient(120deg,#6e5648,#c98e6a 45%,#8a6c5c)" role="img" aria-label="Colleagues smiling while reviewing work at a laptop"></div>
<div class="panel" style="left:736px;top:1056px;width:464px;height:360px;padding:28px 14px 0 14px">
  <h2>Engaging with your talent, that's what we're here</h2>
  <p>With more than a decade of professional experience in Software and Systems Engineering and Technical Lead roles, we're able to correctly distinguish which applicants will be a good match to your organisation.</p>
  <p>Because of our in-depth I.T. experience, understanding of current industry trends, and business connections, we're able to engage with passive job seekers and introduce you to the talent.</p>
  <ul class="ticks">
    <li><svg viewBox="0 0 22 22"><path d="M3 15h16l-2-6-6-4-6 4z" fill="#f37122"/><rect x="2" y="15" width="18" height="3" fill="#f37122"/></svg>Bespoke customer service</li>
    <li><svg viewBox="0 0 22 22"><circle cx="7" cy="7" r="3.5" fill="#f37122"/><circle cx="15" cy="7" r="3.5" fill="#f37122"/><path d="M1 19c0-5 3-8 6-8s6 3 6 8zM9 19c0-5 3-8 6-8s6 3 6 8z" fill="#f37122"/></svg>Forming partnerships</li>
    <li><svg viewBox="0 0 22 22"><circle cx="11" cy="8" r="5" fill="none" stroke="#f37122" stroke-width="3" stroke-dasharray="3 2"/><path d="M2 16h5l5 2h5l4-3v4H2z" fill="#f37122"/></svg>Transparency &amp; honesty</li>
  </ul>
</div>

<div class="panel" style="left:274px;top:1416px;width:462px;height:360px;padding:32px 14px 0 14px">
  <h2>A few reasons for us to work together</h2>
  <ul class="reasons">
    <li><b>Bespoke customer service</b> with a dedicated account manager (a nice one).</li>
    <li><b>We offer a 110% money back guarantee</b> if you're not happy with your talent.</li>
    <li><b>Transparency &amp; honesty</b> when discussing what we can achieve for you (no time-wasting).</li>
    <li><b>Forming partnerships</b> we work in partnership with our clients and strive to be part of their recruitment strategy.</li>
  </ul>
</div>
<div class="photo" style="left:736px;top:1416px;width:464px;height:360px;background:linear-gradient(120deg,#2e3238,#5b5f66 50%,#3a3530)" role="img" aria-label="Coworkers sharing a tablet in a cafe"></div>

<div class="abs portrait" role="img" aria-label="Portrait of the co-founder"></div>
<div class="abs founder">
  <h2>HI I'M MARISOL</h2>
  <div class="rule"></div>
  <div class="lead">I'm a co-founder of Zestio Talent since 2016 and have loved every minute of it.</div>
  <p>Our mission is to help great developers &amp; companies connect. With more than 25 years' combined experience in IT, communication and customer service, we're confident we can help you.</p>
  <p>Whether you're a job-seeker or an employer, we understand the challenges you face. How come, you may ask? We walked in your shoes throughout our careers with some roads being quite bumpy.</p>
</div>

<section class="abs blog"></section>
<h2 class="sec-title" style="top:2150px">OUR BLOG POSTS</h2>
<div class="sec-rule" style="top:2200px"></div>

<div class="card" style="left:302px">
  <div class="img" role="img" aria-label="Colleagues chatting at a desk" style="background:linear-gradient(135deg,#5a6a6e,#a08a7a 55%,#3f4a50)"><div class="date"><div class="m">AUG</div><div class="d">11</div></div></div>
  <h3>Are Jobs Like Fashion?</h3>
  <p>We're glad our experience with some of the recruitment agencies was bumpy otherwise we wouldn't have started Zestio.</p>
  <span class="btn filled">Read More</span>
</div>
<div class="card" style="left:598px">
  <div class="img" role="img" aria-label="Business handshake across a meeting table" style="background:linear-gradient(135deg,#c9ccd0,#6d7279 55%,#9a9ea4)"><div class="date"><div class="m">AUG</div><div class="d" style="background:var(--ink)">20</div></div></div>
  <h3>Diversity For Business</h3>
  <p>We're glad our experience with some of the recruitment agencies was bumpy otherwise we wouldn't have started Zestio.</p>
  <span class="btn">Read More</span>
</div>
<div class="card" style="left:894px">
  <div class="img" role="img" aria-label="Hands sheltering a paper family cutout" style="background:linear-gradient(135deg,#6b5446,#b08a6e 50%,#d9c3ad)"><div class="date"><div class="m">AUG</div><div class="d" style="background:var(--ink)">20</div></div></div>
  <h3>Tech Trends 2017</h3>
  <p>We're glad our experience with some of the recruitment agencies was bumpy otherwise we wouldn't have started Zestio.</p>
  <span class="btn">Read More</span>
</div>

<footer class="abs footer"></footer>
<div class="abs foot-brand"><span class="brand-dot"></span><span class="brand-name">ZESTIO</span></div>
<div class="abs foot-social">
  <div class="diamond-btn"><span></span></div>
  <div class="diamond-btn"><span></span></div>
  <div class="diamond-btn"><span></span></div>
</div>
<div class="abs contact-title">CONTACT US</div>
<div class="abs contact-rule"></div>
<div class="abs contact-line" style="top:2804px"><span class="ico"><svg viewBox="0 0 16 16"><path d="M3 1l3 3-2 2c1 2 3 4 5 5l2-2 3 3-2 3C7 15 1 9 1 3z" fill="#fff"/></svg></span><span><b>TELEPHONE:</b> 0200 555 123</span></div>
<div class="abs contact-line" style="top:2862px"><span class="ico"><svg viewBox="0 0 16 16"><rect x="1" y="3" width="14" height="10" fill="none" stroke="#fff" stroke-width="1.6"/><path d="M1 3l7 6 7-6" fill="none" stroke="#fff" stroke-width="1.4"/></svg></span><span><b>SAY HELLO:</b> info@zestiotalent.com</span></div>
<div class="abs foot-rule"></div>
<div class="abs copyright">Copyright © 2017 Zestio. All Right Reserved</div>

</body>
</html>
```